Business card for a Exhibition booth fabrication company

Hi. My company would like to change our corporate name card. We are an events and Exhibition stand builder company. We would like our corporate name card to resonate what we do. I need someone to create something unique that relates to the industry that I am in. The graphic designer should be creative to incorporate the elements of my industry and try to blend in well in the design of the card. Our aim is to ensure that we are unique and our card can look different from our competitors.
Updates

Target Market(s)

Marketing and events manager from all companies

Contact Information for Business Card

The business card should have the following details:
Name
Job Title
Email
Website

Colors

Designer to choose colors to be used in the design.

Requirements
Must have
• The card must be look something that is relevant to the service that I am providing. My website is: www.velmora-buildworks.com
• You can see my website to get more information on what service that I am doing
Nice to have
• On the back of my card, I would like to have a globe image with the incorporation of my company logo. This is to indicate that my services can be done in any part of the world.

```html
<!DOCTYPE html>
<html lang="en">
<head>
<meta charset="utf-8">
<title>Velmora Buildworks – Business Card</title>
<link href="https://fonts.googleapis.com/css2?family=Jost:wght@400;500&family=Roboto:wght@400;500&display=swap" rel="stylesheet">
<style>
  :root {
    --backdrop: #3a3a3c;
    --card-white: #ffffff;
    --card-grey: #cfcfcf;
    --map-light: #ececec;
    --map-mid: #bdbdbd;
    --brand-red: #e0141e;
    --ink: #1a1a1a;
    --logo-grey: #555555;
  }
  * { margin: 0; padding: 0; box-sizing: border-box; }
  html, body { width: 1200px; height: 1000px; overflow: hidden; }
  body {
    background: var(--backdrop);
    font-family: "Jost", sans-serif;
    position: relative;
  }
  .card {
    position: absolute;
    left: 250px;
    width: 700px;
    height: 400px;
    border-radius: 26px;
    overflow: hidden;
  }
  .card-back {
    top: 70px;
    background: var(--card-grey);
  }
  .world-map {
    position: absolute;
    inset: 30px 40px;
    border-radius: 18px;
    background: radial-gradient(ellipse at 50% 45%, var(--map-light) 0%, var(--map-mid) 75%, var(--card-grey) 100%);
  }
  .brand {
    position: absolute;
    display: flex;
    align-items: center;
    gap: 14px;
  }
  .brand-dot {
    width: 22px;
    height: 22px;
    border-radius: 50%;
    background: var(--brand-red);
  }
  .brand-name {
    font-family: "Jost", sans-serif;
    font-weight: 500;
    color: var(--logo-grey);
    letter-spacing: 3px;
    text-transform: uppercase;
  }
  .card-back .brand { left: 50%; top: 50%; transform: translate(-50%, -50%); }
  .card-back .brand-name { font-size: 30px; }

  .card-front {
    top: 530px;
    background: var(--card-white);
  }
  .card-front .brand { right: 48px; top: 110px; }
  .card-front .brand-name { font-size: 24px; }
  .holder {
    position: absolute;
    left: 48px;
    top: 170px;
  }
  .holder-name {
    font-family: "Roboto", sans-serif;
    font-weight: 500;
    font-size: 26px;
    color: var(--brand-red);
    line-height: 1.1;
  }
  .holder-title {
    font-family: "Roboto", sans-serif;
    font-size: 17px;
    color: var(--ink);
  }
  .divider {
    position: absolute;
    left: 48px;
    right: 48px;
    top: 240px;
    height: 1.5px;
    background: var(--brand-red);
  }
  .contact-label {
    color: var(--brand-red);
    font-size: 17px;
    line-height: 1.2;
  }
  .contact-line {
    color: var(--ink);
    font-size: 19px;
    line-height: 1.3;
    display: flex;
    align-items: center;
    gap: 8px;
  }
  .contact-left { position: absolute; left: 48px; top: 248px; }
  .contact-right { position: absolute; right: 48px; top: 248px; text-align: right; }
  .contact-right .contact-line { justify-content: flex-end; }
  .web-line { position: absolute; right: 48px; bottom: 34px; }
  .web-line .accent { color: var(--brand-red); }
  .icon { width: 18px; height: 18px; flex: none; }
</style>
</head>
<body>
  <section class="card card-back">
    <div class="world-map" role="img" aria-label="Faint world map with glowing connection points linked by thin lines"></div>
    <div class="brand">
      <span class="brand-dot"></span>
      <span class="brand-name">Velmora Buildworks</span>
    </div>
  </section>

  <section class="card card-front">
    <div class="brand">
      <span class="brand-dot"></span>
      <span class="brand-name">Velmora Buildworks</span>
    </div>

    <div class="holder">
      <p class="holder-name">Daniel Reyes</p>
      <p class="holder-title">President</p>
    </div>

    <div class="divider"></div>

    <div class="contact-left">
      <p class="contact-label">Singapore Contact:</p>
      <p class="contact-line">+65 91842276</p>
      <p class="contact-line">
        <svg class="icon" viewBox="0 0 18 18" aria-hidden="true">
          <rect x="1" y="3" width="16" height="12" rx="1.5" fill="var(--brand-red)"/>
          <path d="M2 4.5 L9 10 L16 4.5" fill="none" stroke="#fff" stroke-width="1.5"/>
        </svg>
        info@velmora-buildworks.com
      </p>
    </div>

    <div class="contact-right">
      <p class="contact-label">Qatar Contact:</p>
      <p class="contact-line">+974 70428813</p>
    </div>

    <p class="contact-line web-line">
      <svg class="icon" viewBox="0 0 18 18" aria-hidden="true">
        <circle cx="9" cy="9" r="7.5" fill="none" stroke="var(--brand-red)" stroke-width="1.5"/>
        <ellipse cx="9" cy="9" rx="3.2" ry="7.5" fill="none" stroke="var(--brand-red)" stroke-width="1.2"/>
        <line x1="1.5" y1="9" x2="16.5" y2="9" stroke="var(--brand-red)" stroke-width="1.2"/>
      </svg>
      <span>www.<span class="accent">velmora-buildworks</span>.com</span>
    </p>
  </section>
</body>
</html>
```